Design a calming beauty medical salon & spa website based in Hong Kong

We need help building an informational website for a beauty salon in Hong Kong. The local salon provides facials, massages, body and other slimming treatments in a relaxing environment. We offer some non-invasive medical treatments, such as botox. Having built the business on word of mouth, it is now time for us to launch a website to help market the business better. Website requirements:

-Must be responsive
-Use vibrant but clean colours. not too many, 1-2 colours
-Must be bilingual (switch between Chinese traditional and English)
-Our current website is host on a server, not using any particular platforms like wordpress

Pages:
1/ Homepage
2/ About us (incorporate gallery of salon photos and history of company)
3/ Promotions and latest deals (and leads them to sign up for more info, maybe pop-up small window when you click on a promotion)
4/ Treatment menus
4.1/Body treatments
4.2/ Face treatments
4.3/ Slimming treatments
5/ Showcasing products sold (no e-commerce functionality, just showing off products)
6/ Contact us (tel, address, map, opening hrs)

Footer - must haves include contact us info, privacy policy, terms & conditions, copyright blurb, join our company/employment page (with a form)

For information (comparable websites we like):
http://veltora.com/
http://pambrix.com.hk/tc/aboutpambrix/background.php#centerenvi
Attaching a very first draft concept for this website
Attaching pictures of the beauty salon
Attaching logo

Target Market(s)

Hong Kong based, Chinese, females, 30-50+ age. 90% female clients.

Industry/Entity Type

Beauty Salon

Number of Pages Required

5+ page

Font styles to use
Sans Serif

Colors
f9d9e8
fbd3d4
fee3d5
fbe7d2
fee18a
fbf289
ffffff

Requirements
Must have
• interactive elements on website, such as scrolling banner photo headers
• incorporate photos of website salon
• connect to facebook page

```html
<!DOCTYPE html>
<html lang="en">
<head>
<meta charset="utf-8">
<title>Serena Beauty</title>
<link href="https://fonts.googleapis.com/css2?family=Courgette&family=Open+Sans:wght@400;600;700&display=swap" rel="stylesheet">
<style>
:root{
  --purple:#681877;
  --purple-deep:#561063;
  --title:#5c1170;
  --pink:#f9d9e8;
  --yellow:#fee18a;
  --ink:#3a2a40;
  --grey:#777;
  --white:#fff;
  --script:'Courgette', cursive;
  --sans:'Open Sans', sans-serif;
}
*{box-sizing:border-box;margin:0;padding:0}
html,body{width:1200px;height:3939px;overflow:hidden}
body{font-family:var(--sans);color:var(--ink);background:var(--white);position:relative}
.abs{position:absolute}
.photo{position:absolute}
.btn{position:absolute;background:var(--yellow);color:var(--purple);font-size:17px;letter-spacing:3px;text-transform:uppercase;display:flex;align-items:center;justify-content:center;font-weight:600}

/* header / hero */
.hero{position:absolute;left:0;top:0;width:1200px;height:562px;background:linear-gradient(90deg,#e9c7da 0%,#f0d2e2 45%,#f6dde8 70%,#e8c3d6 100%)}
.hero-model{left:600px;top:0;width:450px;height:562px;background:radial-gradient(ellipse at 55% 45%,#f7e3e0 0%,#ecc8cf 55%,rgba(236,200,215,0) 80%)}
.brand{position:absolute;left:87px;top:28px;display:flex;align-items:center;gap:12px;color:var(--purple);font-size:30px;font-weight:700}
.brand-dot{width:40px;height:40px;border-radius:50%;background:var(--purple)}
.topbar{position:absolute;right:90px;top:38px;display:flex;align-items:center;gap:18px;font-size:14px;color:var(--purple)}
.topbar .dot{width:14px;height:14px;border-radius:50%;background:var(--purple)}
.nav{position:absolute;right:90px;top:70px;display:flex;gap:24px;font-size:17px;color:var(--purple)}
.hero-title{position:absolute;left:87px;top:262px;font-family:var(--script);font-weight:400;font-size:62px;letter-spacing:10px;color:var(--purple)}
.hero-tag{position:absolute;left:87px;top:355px;width:530px;height:40px;background:var(--purple);color:var(--white);font-size:24px;letter-spacing:7px;display:flex;align-items:center;justify-content:center}
.dots{position:absolute;display:flex;gap:8px}
.dots i{width:18px;height:18px;border-radius:50%;background:#d6b2cf;display:block}
.dots i:first-child{background:var(--purple)}

/* section titles */
.sec-title{position:absolute;left:87px;width:1026px;display:flex;align-items:center;gap:24px}
.sec-title .rule{flex:1;height:8px;border-top:2px dotted #c9c9c9;border-bottom:2px dotted #c9c9c9}
.sec-title h2{font-family:var(--script);font-weight:400;font-size:44px;color:var(--title)}
.sec-title.light .rule{border-color:rgba(255,255,255,.45)}
.sec-title.light h2{color:var(--white)}

/* about */
.about{position:absolute;left:0;top:562px;width:1200px;height:462px;background:linear-gradient(90deg,#ece6e4 0%,#f6f2ef 40%,#faf8f6 70%,#f1ece9 100%)}
.circle-photo{position:absolute;border-radius:50%;border:6px solid var(--white);box-shadow:0 2px 8px rgba(0,0,0,.15)}
.about-text{position:absolute;left:612px;top:727px;width:395px;font-size:14.5px;line-height:21px;color:#555}

/* treatments */
.treatments{position:absolute;left:0;top:1024px;width:1200px;height:1221px;background:var(--purple)}
.t-text{position:absolute;width:410px;color:var(--white)}
.t-text h3{font-size:17px;font-weight:700;letter-spacing:.5px;margin-bottom:8px}
.t-text p{font-size:14px;line-height:22px;margin-bottom:14px}
.t-text ul{list-style:none}
.t-text li{font-size:14px;display:flex;align-items:center;gap:18px;height:34px}
.t-text li i{width:18px;height:12px;background:var(--yellow);border-radius:9px 9px 2px 2px;display:block}
.t-text .btn{position:static;width:175px;height:44px;margin-top:20px}
.t-img{position:absolute;width:413px;height:302px}
.t-img span{position:absolute;left:0;bottom:0;width:100%;height:48px;background:#1c1c1c;color:var(--white);font-size:21px;letter-spacing:4px;display:flex;align-items:center;justify-content:center}
.t-sep{position:absolute;left:173px;width:854px;height:1px;background:rgba(255,255,255,.22)}

/* products */
.prod{position:absolute;top:2390px;width:178px;display:flex;flex-direction:column;align-items:center}
.prod .ph{width:178px;height:178px;border-radius:50%;border:2px solid #eee}
.prod h4{margin-top:26px;font-size:16px;font-weight:700;letter-spacing:1px;color:var(--purple);white-space:nowrap}

/* testimonial */
.testi-name{position:absolute;left:0;width:1200px;top:2984px;text-align:center;font-size:17px;font-weight:700;letter-spacing:2px;color:var(--purple)}
.testi-text{position:absolute;left:300px;width:600px;top:3012px;text-align:center;font-size:14px;line-height:22px;color:var(--grey)}

/* promos */
.promo{position:absolute;top:3175px;width:600px;height:294px}
.promo-copy{position:absolute;left:87px;top:55px}
.promo-copy h3{font-size:30px;font-weight:400;letter-spacing:3px;line-height:34px}
.promo-copy .offer{font-family:var(--script);font-size:46px;color:var(--yellow);margin-top:4px}
.promo-copy a{display:inline-block;margin-top:18px;font-size:16px;letter-spacing:2px;text-decoration:underline;color:inherit}

/* contact */
.contact{position:absolute;left:0;top:3469px;width:1200px;height:347px;background:var(--pink)}
.contact-head{position:absolute;top:3502px;font-family:var(--script);font-weight:400;font-size:27px;color:var(--purple)}
.field{position:absolute;left:87px;width:330px;border-bottom:1px solid #d8b7c9;height:40px;display:flex;align-items:center;gap:16px;font-size:14px;color:#666}
.field svg{width:14px;height:14px;fill:var(--purple)}
.hours{position:absolute;left:507px;font-size:14px;line-height:24px;color:#333}
.hours b{font-weight:700}
.info-row{position:absolute;left:793px;display:flex;align-items:center;gap:18px;font-size:14px;line-height:22px;color:#333;width:340px}
.info-row .ic{flex:none;width:30px;height:30px;border-radius:50%;background:var(--purple);display:flex;align-items:center;justify-content:center}
.info-row .ic svg{width:16px;height:16px;fill:var(--white)}
.hotline-label{position:absolute;left:793px;top:3710px;font-size:17px;font-weight:700;letter-spacing:1px;color:#222}
.hotline{position:absolute;left:793px;top:3738px;font-family:var(--script);font-size:30px;color:var(--purple);letter-spacing:2px}

/* footer */
.footer{position:absolute;left:0;top:3816px;width:1200px;height:123px;background:var(--purple);color:var(--white);text-align:center}
.footer .name{position:absolute;left:0;width:1200px;top:26px;font-size:24px;font-weight:700;display:flex;justify-content:center;align-items:center;gap:10px}
.footer .name i{width:28px;height:28px;border-radius:50%;background:var(--white);display:block}
.footer .copy{position:absolute;left:0;width:1200px;top:84px;font-size:13px;letter-spacing:1px}
</style>
</head>
<body>

<!-- Hero -->
<header class="hero">
  <div class="photo" style="left:0;top:0;width:1200px;height:562px;background:linear-gradient(90deg,rgba(200,150,180,.35),rgba(240,210,225,.1) 60%,rgba(190,140,170,.35))" role="img" aria-label="Soft-focus photo of the salon interior in pink tones"></div>
  <div class="photo hero-model" role="img" aria-label="Photo of a smiling woman touching her cheek"></div>
  <div class="brand"><span class="brand-dot"></span>Serena Beauty</div>
  <div class="topbar">
    <svg width="14" height="14" viewBox="0 0 24 24" fill="currentColor"><path d="M6.6 10.8a15.1 15.1 0 0 0 6.6 6.6l2.2-2.2c.3-.3.7-.4 1-.2 1.1.4 2.3.6 3.6.6.6 0 1 .4 1 1V20c0 .6-.4 1-1 1A17 17 0 0 1 3 4c0-.6.4-1 1-1h3.5c.6 0 1 .4 1 1 0 1.3.2 2.5.6 3.6.1.3 0 .7-.2 1z"/></svg>
    <span>TEL: 2480 1357</span><span>|</span><span>WHATSAPP: 6312 9046</span>
    <span class="dot"></span><span>EN ▾</span>
  </div>
  <nav class="nav"><span>Home</span><span>About Us</span><span>Promotions and Latest Deals</span><span>Treatment</span><span>Products</span><span>Contact us</span></nav>
  <h1 class="hero-title">Serena Beauty</h1>
  <div class="hero-tag">EXCELLENT MEDICAL BEAUTY</div>
  <div class="dots" style="left:562px;top:524px"><i></i><i></i><i></i></div>
</header>

<!-- About -->
<section class="about">
  <div class="photo" style="left:0;top:0;width:1200px;height:462px;background:linear-gradient(90deg,rgba(220,205,200,.5),rgba(255,255,255,0) 55%)" role="img" aria-label="Faded photo of a woman relaxing during a spa treatment"></div>
</section>
<div class="sec-title" style="top:615px"><span class="rule"></span><h2>About Us</h2><span class="rule"></span></div>
<div class="circle-photo" style="left:162px;top:682px;width:218px;height:218px;background:linear-gradient(135deg,#d9c2b8,#f1e4de)" role="img" aria-label="Photo of a woman receiving a facial treatment"></div>
<div class="circle-photo" style="left:308px;top:756px;width:210px;height:210px;background:linear-gradient(135deg,#e7d3c9,#c9a89a)" role="img" aria-label="Photo of a cupping therapy treatment on a back"></div>
<p class="about-text">Serena Beauty has been open for business since May 2011. As our name suggests, we are dedicated to providing your beauty with the best quality in every facet. We have gathered a skillful team of beauty specialist to bring to you the most professionals and current beautifying equipment and products.</p>
<div class="btn" style="left:612px;top:866px;width:176px;height:44px">Read More</div>

<!-- Treatments -->
<section class="treatments"></section>
<div class="sec-title light" style="top:1077px"><span class="rule"></span><h2>Treatments</h2><span class="rule"></span></div>

<div class="t-text" style="left:173px;top:1183px">
  <h3>LOREM IPSUM IS SIMPLY DUMMY STANDARD</h3>
  <p>Lorem Ipsum is simply dummy text of the printing and typesetting industry. Lorem Ipsum has been the industry's standard dummy.</p>
  <ul><li><i></i>It is a long established fact that a reader.</li><li><i></i>It is a long established fact.</li><li><i></i>It is a long established fact lorem.</li></ul>
  <div class="btn">Read More</div>
</div>
<div class="t-img" style="left:614px;top:1168px;background:linear-gradient(135deg,#cfc6bc,#8d7f72)" role="img" aria-label="Photo of a woman receiving a back massage"><span>BODY TREATMENT</span></div>

<div class="t-sep" style="top:1496px"></div>

<div class="t-img" style="left:173px;top:1523px;background:linear-gradient(135deg,#e6cfbf,#b9917a)" role="img" aria-label="Photo of a woman receiving a facial massage"><span>FACE TREATMENT</span></div>
<div class="t-text" style="left:614px;top:1538px">
  <h3>LOREM IPSUM IS SIMPLY DUMMY STANDARD</h3>
  <p>Lorem Ipsum is simply dummy text of the printing and typesetting industry. Lorem Ipsum has been the industry's standard dummy.</p>
  <ul><li><i></i>It is a long established fact that a reader.</li><li><i></i>It is a long established fact.</li><li><i></i>It is a long established fact lorem.</li></ul>
  <div class="btn">Read More</div>
</div>

<div class="t-sep" style="top:1851px"></div>

<div class="t-text" style="left:173px;top:1903px">
  <h3>LOREM IPSUM IS SIMPLY DUMMY STANDARD</h3>
  <p>Lorem Ipsum is simply dummy text of the printing and typesetting industry. Lorem Ipsum has been the industry's standard dummy.</p>
  <ul><li><i></i>It is a long established fact that a reader.</li><li><i></i>It is a long established fact.</li><li><i></i>It is a long established fact lorem.</li></ul>
  <div class="btn">Read More</div>
</div>
<div class="t-img" style="left:614px;top:1888px;background:linear-gradient(135deg,#f2f2f2,#d9c2c8 60%,#e2507e)" role="img" aria-label="Photo of a waist being measured with a tape measure"><span>SLIMMING TREATMENT</span></div>

<!-- Products -->
<div class="sec-title" style="top:2299px"><span class="rule"></span><h2>Products</h2><span class="rule"></span></div>
<div class="prod" style="left:115px"><div class="ph" style="background:radial-gradient(circle,#f5e7a0,#d8d0c4 60%,#fff 75%)" role="img" aria-label="Photo of spa stones with a yellow flower"></div><h4>LOREM IPSUM</h4></div>
<div class="prod" style="left:380px"><div class="ph" style="background:radial-gradient(circle,#c9965e,#ece2d4 60%,#fff 75%)" role="img" aria-label="Photo of serum bottles"></div><h4>CONTRATY POLPULAR</h4></div>
<div class="prod" style="left:643px"><div class="ph" style="background:radial-gradient(circle,#f09a3e,#c7b8dc 55%,#fff 75%)" role="img" aria-label="Photo of a purple soap dish with an orange flower"></div><h4>ALL THE LOREM</h4></div>
<div class="prod" style="left:906px"><div class="ph" style="background:radial-gradient(circle,#ffffff,#f4cfd9 60%,#fff 75%)" role="img" aria-label="Photo of a jar of face cream"></div><h4>IPSUM LOREM</h4></div>
<div class="btn" style="left:515px;top:2646px;width:173px;height:45px">View All</div>

<!-- Testimonial -->
<div class="sec-title" style="top:2742px"><span class="rule"></span><h2>Testimonial</h2><span class="rule"></span></div>
<div class="abs" style="left:541px;top:2849px;width:118px;height:118px;border-radius:50%;background:linear-gradient(180deg,#e8e2dc,#3a3036)" role="img" aria-label="Portrait photo of the client"></div>
<div class="testi-name">JANE DOE</div>
<p class="testi-text">Lorem Ipsum has been the industry's standard dummy text ever since the when an unknown printer took a galley of type and scrub.</p>
<div class="dots" style="left:562px;top:3095px"><i></i><i></i><i></i></div>

<!-- Promotions -->
<div class="promo" style="left:0;background:linear-gradient(90deg,#1a1a1a 0%,#2a2228 50%,#6b3f63 100%)" role="img" aria-label="Photo of flower petals and spa stones">
  <div class="promo-copy" style="color:var(--white)"><h3>FLOWER SKIN<br>TREATMENT</h3><div class="offer">50 % Offer</div><a>SIGN UP NOW</a></div>
</div>
<div class="promo" style="left:600px;background:linear-gradient(90deg,#f3eeeb 0%,#ece1dc 45%,#d9b9ad 100%)" role="img" aria-label="Photo of a smiling woman resting her head on her hands">
  <div class="promo-copy" style="left:42px;color:#222"><h3>FULL BODY<br>TREATMENT</h3><div class="offer" style="color:var(--purple)">35 % Offer</div><a>SIGN UP NOW</a></div>
</div>

<!-- Contact -->
<section class="contact"></section>
<h3 class="contact-head" style="left:87px">Contact Form</h3>
<div class="field" style="top:3548px"><svg viewBox="0 0 24 24"><circle cx="12" cy="7" r="5"/><path d="M2 23c0-6 4-9 10-9s10 3 10 9z"/></svg>Name</div>
<div class="field" style="top:3592px"><svg viewBox="0 0 24 24"><path d="M1 5h22v14H1z"/></svg>Email</div>
<div class="field" style="top:3660px"><svg viewBox="0 0 24 24"><path d="M2 3h20v14H8l-6 5z"/></svg>Message</div>
<div class="btn" style="left:87px;top:3723px;width:128px;height:44px">Submit</div>

<h3 class="contact-head" style="left:507px">Opening Hours</h3>
<div class="hours" style="top:3550px"><b>Monday to Friday</b><br>10.30 AM to 9.30 PM</div>
<div class="hours" style="top:3612px"><b>Stuarday and Holidays</b><br>10.30 AM to 7.30 PM</div>
<div class="abs" style="left:507px;top:3692px;width:170px;height:1px;background:#d8b7c9"></div>
<div class="hours" style="top:3708px;font-size:13px;line-height:20px"><b>Privacy Policy<br>Terms &amp; Conditions<br>Join us</b></div>

<h3 class="contact-head" style="left:793px">Contact Info</h3>
<div class="info-row" style="top:3546px"><span class="ic"><svg viewBox="0 0 24 24"><path d="M12 1a8 8 0 0 0-8 8c0 6 8 14 8 14s8-8 8-14a8 8 0 0 0-8-8zm0 11a3 3 0 1 1 0-6 3 3 0 0 1 0 6z"/></svg></span><span>12th Floor, Harbour Lotus Tower, 21-23 Carnarvon Road Tsim Sha Tsui, Kowloon</span></div>
<div class="info-row" style="top:3626px"><span class="ic"><svg viewBox="0 0 24 24"><path d="M2 5h20v14H2zm2 2v1l8 5 8-5V7l-8 5z"/></svg></span><span>hello@serenabeauty.com.hk</span></div>
<div class="info-row" style="top:3668px"><span class="ic"></span><span>Follow us online</span></div>
<div class="hotline-label">INQUIRY HOTLINE:</div>
<div class="hotline">24801357 / 63129046</div>

<!-- Footer -->
<footer class="footer">
  <div class="name"><i></i>Serena Beauty</div>
  <div class="copy">Copyright © 2017 &nbsp;|&nbsp; All Rights Reserved.</div>
</footer>

</body>
</html>
```